BVL - New Homepage needed for an existing website

Bright Valley Lantern Website
Need a new Homepage for an existing website with Action Items and Newer Pictures
This is the current Website
https://brightvalleylantern.example/

This new page will be changed on Jan 21st when Voting begins
1. Voting like a political campaign where we are trying to raise awareness for the issues we stand for and urge the people to go to a Polling /voting website and vote for us (Roster 4)
2. We have 6 basic themes as to what we stand for - there will be text to promote their importance of voting/call to action
3. There will be videos on the website and there will be a simulation of how the voting process works - will be added later

Use colors like the US Flag - Red, White and Blue. The other pages don't need to be changed - only the HomePage.

I only need the design, I will code the website. Thank you

Target Market(s)

Jewish People in the US

Industry/Entity Type

Religious

Number of Pages Required

1 page

Font styles to use
Serif
Sans Serif

Colors

Designer to choose colors to be used in the design.

Requirements
Must have
• Call to Action - Go out to Vote
• This is the current Website - https://brightvalleylantern.example/

```html
<!DOCTYPE html>
<html lang="en">
<head>
<meta charset="utf-8">
<title>Bright Valley Lantern — Home</title>
<link rel="stylesheet" href="https://fonts.googleapis.com/css2?family=Heebo:wght@400;500;700&family=Marcellus&display=swap">
<style>
:root{
  --navy:#0b0b5c;
  --red:#d1111a;
  --red-deep:#b50d14;
  --white:#ffffff;
  --ink:#333333;
  --muted:#666666;
  --footer:#1b1b1b;
  --serif:'Marcellus', Georgia, serif;
  --sans:'Heebo', Arial, sans-serif;
}
*{margin:0;padding:0;box-sizing:border-box}
html,body{width:1200px;height:4673px;overflow:hidden}
body{position:relative;background:var(--white);font-family:var(--sans);color:var(--ink)}
.abs{position:absolute}
a{color:inherit}

.site-header{left:0;top:0;width:1200px;height:112px;background:var(--white)}
.brand{left:90px;top:40px;display:flex;align-items:center;gap:10px;font-weight:700;font-size:17px;color:var(--red-deep);white-space:nowrap}
.brand-mark{width:18px;height:18px;background:var(--red-deep)}
.btn{display:flex;align-items:center;justify-content:center;border-radius:30px;font-family:var(--sans);font-weight:500;white-space:nowrap}
.btn-subscribe{left:482px;top:36px;width:149px;height:44px;background:var(--navy);color:var(--white);font-size:18px}
.btn-login{left:643px;top:36px;width:146px;height:44px;border:2px solid var(--navy);color:var(--navy);font-size:18px}
.call{left:822px;top:38px;display:flex;align-items:center;gap:6px;color:var(--red);font-size:18px;white-space:nowrap}
.call b{font-size:26px;font-weight:500}
.call span{color:var(--ink);font-size:16px;margin-right:4px}

.main-nav{left:0;top:112px;width:1200px;height:48px;background:var(--navy);color:var(--white);font-size:15px}
.main-nav span{position:absolute;top:14px;white-space:nowrap}
.main-nav .current{font-weight:700}

.hero{left:0;top:160px;width:1200px;height:598px;background:radial-gradient(circle at 25% 45%,#c9b69a 0%,#8f8372 28%,#3c3024 55%,#1b140e 80%)}
.hero-kicker{left:569px;top:276px;font-family:var(--serif);font-size:28px;color:var(--white)}
.hero-title{left:559px;top:328px;font-weight:700;font-size:86px;line-height:86px;color:var(--white)}
.btn-hero-red{left:569px;top:529px;width:297px;height:55px;background:var(--red);color:var(--white);font-size:17px}
.btn-hero-blue{left:883px;top:529px;width:150px;height:55px;background:var(--navy);color:var(--white);font-size:17px}
.slider-arrow{width:52px;height:52px;border-radius:50%;display:flex;align-items:center;justify-content:center}
.slider-prev{left:19px;top:424px;background:var(--red)}
.slider-next{left:1130px;top:424px;background:#222}

.mission-star{left:94px;top:861px;width:400px;height:459px}
.mission-title{left:580px;top:912px;font-family:var(--serif);font-weight:400;font-size:38px;color:var(--navy);white-space:nowrap}
.mission-sub{left:587px;top:964px;font-weight:500;font-size:22px;color:var(--red)}
.mission-text{left:587px;top:1014px;width:560px;font-size:16px;line-height:34px;color:var(--muted);white-space:nowrap}
.btn-read{left:587px;top:1211px;width:153px;height:45px;background:var(--red);color:var(--white);font-size:16px}

.embrace-band{left:0;top:1414px;width:1200px;height:544px;background:linear-gradient(90deg,#1e2a86 0%,#3b4aa6 35%,#2c3a96 70%,#1a2478 100%)}
.embrace-title{left:0;top:1508px;width:1200px;text-align:center;font-family:var(--serif);font-weight:400;font-size:38px;line-height:48px;color:var(--white)}
.video{left:261px;top:1650px;width:678px;height:397px;background:linear-gradient(120deg,#9b9b9b 0%,#4a4a4a 45%,#1c1c1c 100%)}
.play{left:570px;top:1831px;width:60px;height:40px;border-radius:10px;background:var(--red);display:flex;align-items:center;justify-content:center}

.points-title{left:0;top:2137px;width:1200px;text-align:center;font-family:var(--serif);font-weight:400;font-size:38px;color:var(--navy)}
.points-title em{font-style:normal;color:var(--red)}
.hexagram{left:0;top:2200px;width:1200px;height:960px}
.pt{position:absolute;transform:translateX(-50%);text-align:center;font-weight:500;font-size:24px;line-height:31px;color:#222;white-space:nowrap}
.pt-light{color:var(--white)}
.objectives{left:380px;top:2505px;width:440px;text-align:center;color:var(--white)}
.objectives h3{font-weight:400;font-size:22px;letter-spacing:.5px;margin-bottom:20px}
.objectives p{font-size:17px;line-height:40px}
.objectives a{display:inline-block;margin-top:14px;font-weight:500;font-size:17px;text-decoration:underline}

.quote-band{left:0;top:3212px;width:1200px;height:537px;background:linear-gradient(90deg,#d8141c 0%,#c8121a 55%,#b50e15 100%)}
.quote-text{left:89px;top:3365px;width:720px;font-weight:500;font-size:34px;line-height:53px;color:var(--white);white-space:nowrap}
.quote-by{left:89px;top:3563px;font-family:var(--serif);font-size:31px;color:var(--white)}
.quote-photo{left:734px;top:3308px;width:412px;height:356px}

.join-photo{left:105px;top:3852px;width:421px;height:362px}
.join-title{left:600px;top:3860px;font-family:var(--serif);font-weight:400;font-size:40px;color:var(--navy);white-space:nowrap}
.join-title em{font-style:normal;color:var(--red)}
.join-text{left:600px;top:3930px;width:500px;font-size:17px;line-height:29px;color:var(--muted)}
.field{width:237px;height:47px;border:1px solid #ddd;padding-left:20px;display:flex;align-items:center;font-size:13px;color:#aaa}
.btn-action{left:600px;top:4148px;width:160px;height:47px;background:var(--red);color:var(--white);font-size:16px}

.site-footer{left:0;top:4314px;width:1200px;height:359px;background:var(--footer);color:#d8d8d8}
.foot-head{font-family:var(--serif);font-size:20px;color:var(--white)}
.foot-list{font-size:13.5px;line-height:28px;white-space:nowrap}
.copyright{left:0;top:4628px;width:1200px;text-align:center;font-size:12px;color:#cfcfcf}
.edge{left:0;width:1200px;height:40px}
</style>
</head>
<body>

<header class="abs site-header">
  <div class="abs brand"><span class="brand-mark"></span>Bright Valley Lantern</div>
  <div class="abs btn btn-subscribe">Subscribe</div>
  <div class="abs btn btn-login">Login</div>
  <div class="abs call">
    <svg width="18" height="18" viewBox="0 0 24 24"><path fill="#d1111a" d="M6.6 10.8a15.2 15.2 0 0 0 6.6 6.6l2.2-2.2c.3-.3.7-.4 1-.2 1.1.4 2.3.6 3.6.6.6 0 1 .4 1 1V20c0 .6-.4 1-1 1A17 17 0 0 1 3 4c0-.6.4-1 1-1h3.5c.6 0 1 .4 1 1 0 1.3.2 2.5.6 3.6.1.3 0 .7-.2 1z"/></svg>
    <span>Call Us</span><b>+ 1 555 010 0200</b>
  </div>
</header>

<nav class="abs main-nav">
  <span class="current" style="left:101px">Confront Anti–Semitism</span>
  <span style="left:319px">Expose BDS</span>
  <span style="left:448px">Instill Jewish Pride</span>
  <span style="left:620px">Maintain Israel's Jewish Identity</span>
  <span style="left:886px">Resist Assimilation</span>
  <span style="left:1062px">More</span>
</nav>

<section class="abs hero" role="img" aria-label="Photo of a child wearing a kippah beside glowing menorah candles"></section>
<div class="abs hero-kicker">IT'S ALL ABOUT</div>
<h1 class="abs hero-title">JEWISH<br>CONTINUITY</h1>
<div class="abs btn btn-hero-red">New Law Increases Hate Crimes</div>
<div class="abs btn btn-hero-blue">Go Out to Vote</div>
<div class="abs slider-arrow slider-prev"><svg width="16" height="16" viewBox="0 0 16 16"><path d="M11 2 5 8l6 6" fill="none" stroke="#fff" stroke-width="3"/></svg></div>
<div class="abs slider-arrow slider-next"><svg width="16" height="16" viewBox="0 0 16 16"><path d="m5 2 6 6-6 6" fill="none" stroke="#fff" stroke-width="3"/></svg></div>
<svg class="abs edge" style="top:722px" viewBox="0 0 1200 40" preserveAspectRatio="none"><path fill="#fff" d="M0 40V22L60 28 120 16 180 26 240 18 300 30 360 16 420 24 480 18 540 28 600 16 660 24 720 18 780 30 840 20 900 26 960 18 1020 28 1080 16 1140 24 1200 18V40Z"/></svg>

<section>
  <svg class="abs mission-star" viewBox="0 0 400 459" role="img" aria-label="Photo of worshippers at the Western Wall framed in a six-pointed star">
    <defs><linearGradient id="wall" x1="0" y1="0" x2="0" y2="1"><stop offset="0" stop-color="#cbbb9c"/><stop offset=".6" stop-color="#a8967a"/><stop offset="1" stop-color="#6b5f50"/></linearGradient></defs>
    <path fill="url(#wall)" fill-rule="evenodd" d="M200 0 265 114 400 114 333 230 400 345 265 345 200 459 135 345 0 345 67 230 0 114 135 114Z M135 114 265 114 333 230 265 345 135 345 67 230Z"/>
  </svg>
  <h2 class="abs mission-title">BRIGHT VALLEY LANTERN</h2>
  <div class="abs mission-sub">MISSION STATEMENT</div>
  <p class="abs mission-text">Bright Valley Lantern is a grassroots movement that was established to<br>promote Jewish Continuity, recognizing that in the United States,<br>Judaism and its continuity are under attack for a host of reasons, all<br>of which Bright Valley Lantern believes must be identified, understood,<br>and addressed in the appropriate manner.</p>
  <div class="abs btn btn-read">Read More</div>
</section>

<section>
  <div class="abs embrace-band" role="img" aria-label="Photo of a man in a prayer shawl reading, tinted blue"></div>
  <svg class="abs edge" style="top:1404px" viewBox="0 0 1200 40" preserveAspectRatio="none"><path fill="#fff" d="M0 0V24L60 16 120 28 180 18 240 26 300 14 360 24 420 18 480 30 540 20 600 28 660 16 720 26 780 20 840 28 900 18 960 30 1020 22 1080 28 1140 18 1200 24V0Z"/></svg>
  <svg class="abs edge" style="top:1930px" viewBox="0 0 1200 40" preserveAspectRatio="none"><path fill="#fff" d="M0 40V18L60 26 120 16 180 28 240 20 300 30 360 18 420 24 480 14 540 26 600 18 660 28 720 16 780 26 840 20 900 28 960 18 1020 30 1080 20 1140 26 1200 18V40Z"/></svg>
  <h2 class="abs embrace-title">WE EMBRACE OUR PAST TO<br>ENSURE OUR FUTURE</h2>
  <div class="abs video" role="img" aria-label="Video still of a speaker in black and white"></div>
  <div class="abs play"><svg width="18" height="18" viewBox="0 0 18 18"><path d="M4 2v14l11-7z" fill="#fff"/></svg></div>
</section>

<section>
  <h2 class="abs points-title">6 POINTS. 5 MINUTES. <em>1 BOLD NEW MOVEMENT.</em></h2>
  <svg class="abs hexagram" viewBox="0 0 1200 960">
    <path d="M600 21 196 695H1004Z" fill="none" stroke="#e4e4e4" stroke-width="16"/>
    <path d="M196 231H1004L600 931Z" fill="none" stroke="#e4e4e4" stroke-width="16"/>
    <path d="M600 40 486 231H714Z" fill="#d1111a"/>
    <path d="M475 251H725L847 465 725 679H475L352 465Z" fill="#0b0b5c"/>
  </svg>
  <div class="pt pt-light" style="left:600px;top:2354px">Resist<br>Assimilation</div>
  <div class="pt" style="left:341px;top:2466px">Expose<br>BDS</div>
  <div class="pt" style="left:859px;top:2466px">Confront Anti–<br>Semitism</div>
  <div class="pt" style="left:341px;top:2803px">Instill<br>Jewish Pride</div>
  <div class="pt" style="left:852px;top:2803px">The Eternal<br>Jewish Homeland</div>
  <div class="pt" style="left:600px;top:2913px">Maintain<br>Israel's Jewish<br>Identity</div>
  <div class="abs objectives">
    <h3>OBJECTIVES</h3>
    <p>Assimilation is an issue facing<br>every religion. With respect to Judaism,<br>Bright Valley Lantern underscores the need for<br>education regarding our history, heritage<br>and the beauty of Judaism.</p>
    <a>Discover More</a>
  </div>
</section>

<section>
  <div class="abs quote-band" role="img" aria-label="Photo of a grand synagogue interior, tinted red"></div>
  <svg class="abs edge" style="top:3202px" viewBox="0 0 1200 40" preserveAspectRatio="none"><path fill="#fff" d="M0 0V20L60 28 120 18 180 30 240 22 300 28 360 16 420 26 480 20 540 30 600 18 660 26 720 20 780 30 840 18 900 26 960 20 1020 28 1080 16 1140 26 1200 20V0Z"/></svg>
  <svg class="abs edge" style="top:3716px" viewBox="0 0 1200 40" preserveAspectRatio="none"><path fill="#fff" d="M0 40V20L60 12 120 24 180 14 240 22 300 10 360 20 420 14 480 24 540 12 600 20 660 14 720 26 780 16 840 22 900 12 960 22 1020 14 1080 24 1140 14 1200 20V40Z"/></svg>
  <p class="abs quote-text">"By Connecting Jews To Their Heritage,<br>History And Faith, We Can Ensure That Global<br>Jewry Not Only Survives, But Surges."</p>
  <div class="abs quote-by">BRIGHT VALLEY LANTERN</div>
  <svg class="abs quote-photo" viewBox="0 0 412 356" role="img" aria-label="Aerial photo of synagogue pews framed in a triangle">
    <defs><linearGradient id="pews" x1="0" y1="0" x2="0" y2="1"><stop offset="0" stop-color="#e2c79a"/><stop offset=".5" stop-color="#b88a55"/><stop offset="1" stop-color="#6e4a2a"/></linearGradient></defs>
    <path d="M205 0 412 356H0Z" fill="url(#pews)"/>
  </svg>
</section>

<section>
  <svg class="abs join-photo" viewBox="0 0 421 362" role="img" aria-label="Photo of a man wrapped in a striped prayer shawl framed in a triangle">
    <defs><linearGradient id="tallit" x1="0" y1="0" x2="1" y2="1"><stop offset="0" stop-color="#b9a48a"/><stop offset=".5" stop-color="#e9e6e0"/><stop offset="1" stop-color="#4a4d5a"/></linearGradient></defs>
    <path d="M210 0 421 362H0Z" fill="url(#tallit)"/>
  </svg>
  <h2 class="abs join-title">JOIN THE <em>JEWISH FUTURE</em></h2>
  <p class="abs join-text">Help us ensure a world Jewish platform that keeps our people and communities strong, safe and proud.</p>
  <div class="abs field" style="left:600px;top:4021px">Name</div>
  <div class="abs field" style="left:850px;top:4021px">Email Address</div>
  <div class="abs field" style="left:600px;top:4084px">Phone Number</div>
  <div class="abs field" style="left:850px;top:4084px">City</div>
  <div class="abs btn btn-action">Go Out to Vote</div>
</section>

<footer class="abs site-footer">
  <div class="abs foot-head" style="left:92px;top:102px">OUR SERVICES</div>
  <div class="abs foot-list" style="left:92px;top:142px">Resist Assimilation<br>Confront Anti–Semitism<br>Expose BDS<br>Instill Jewish Pride</div>
  <div class="abs foot-list" style="left:295px;top:142px">Israel: The Eternal Jewish Homeland<br>Maintain Israel's Jewish Identity</div>
  <div class="abs foot-head" style="left:605px;top:102px">Jewish Continuity</div>
  <div class="abs foot-list" style="left:605px;top:142px">Israel is the geographical<br>anchor of Judaism, the Torah is<br>the ideological/theological<br>anchor of Judaism</div>
  <div class="abs foot-head" style="left:906px;top:102px">Contact</div>
  <div class="abs foot-list" style="left:906px;top:144px">
    <div style="display:flex;align-items:center;gap:10px"><svg width="14" height="14" viewBox="0 0 24 24"><path fill="#fff" d="M6.6 10.8a15.2 15.2 0 0 0 6.6 6.6l2.2-2.2c.3-.3.7-.4 1-.2 1.1.4 2.3.6 3.6.6.6 0 1 .4 1 1V20c0 .6-.4 1-1 1A17 17 0 0 1 3 4c0-.6.4-1 1-1h3.5c.6 0 1 .4 1 1 0 1.3.2 2.5.6 3.6.1.3 0 .7-.2 1z"/></svg>(+1 555 010 0200)</div>
    <div style="display:flex;align-items:center;gap:10px"><svg width="14" height="12" viewBox="0 0 14 12"><rect x="1" y="1" width="12" height="10" fill="none" stroke="#fff" stroke-width="1.6"/><path d="m1 1 6 5 6-5" fill="none" stroke="#fff" stroke-width="1.4"/></svg><a style="text-decoration:underline">info@brightvalleylantern.example</a></div>
  </div>
</footer>
<svg class="abs edge" style="top:4290px" viewBox="0 0 1200 40" preserveAspectRatio="none"><path fill="#1b1b1b" d="M0 40V22L60 12 120 24 180 16 240 26 300 14 360 20 420 12 480 24 540 14 600 22 660 16 720 26 780 14 840 22 900 16 960 26 1020 14 1080 22 1140 16 1200 24V40Z"/></svg>
<div class="abs copyright">© 2020 Copyrights. Bright Valley Lantern. All rights reserved</div>

</body>
</html>
```